Erstellung eines Polizeiwimpels für Kinder
Zielgruppe
Wir stellen Fahrradwimpel für Kinder her. Hier finden Sie unsere Produkte: https://www.kaufhalle-wiro.de/laden/regal/58203917462
Aufgabenstellung
Wir möchten einen 'Polizeiwimpel' für Kinder herstellen.
Wenn möglich, nur eine Farbe verwenden (reduziert Kosten in der Produktion). Der Hintergrund soll 'Polizei Blau' sein.
Wimpelgröße: 17,5 cm X 32 cm X 32cm (Dreieckig)
Ich habe ein selbst erstelltes Design hochgeladen. Es soll den Schriftzug 'Polizei' enthalten und evtl. noch 'Polizei Symbole', die Jungs (und ihre Eltern) ansprechen. (Pistole, Sheriffstern, etc.) Das offizielle Wappen oder andere Hoheitssymbole dürfen wir allerdings nicht verwenden.

```html
<!DOCTYPE html>
<html lang="de">
<head>
<meta charset="utf-8">
<title>Polizeiwimpel – Druckbogen</title>
<link rel="stylesheet" href="https://fonts.googleapis.com/css2?family=Arimo:wght@700&display=swap">
<style>
  :root {
    --polizei-blau: #035da2;
    --weiss: #ffffff;
    --schnittlinie: #a8a8a8;
    --papier: #ffffff;
  }
  html, body {
    margin: 0;
    padding: 0;
    width: 1200px;
    height: 960px;
    overflow: hidden;
    background: var(--papier);
  }
  .druckbogen {
    display: block;
    width: 1200px;
    height: 960px;
  }
  .schnittlinie {
    stroke: var(--schnittlinie);
    stroke-width: 0.7;
    stroke-dasharray: 1.5 1.5;
  }
  .wimpel-flaeche { fill: var(--polizei-blau); }
  .stern-feld { fill: var(--weiss); }
  .wimpel-titel {
    font-family: "Arimo", Arial, sans-serif;
    font-weight: 700;
    font-size: 50px;
    fill: var(--weiss);
  }
  .wimpel-web {
    font-family: "Arimo", Arial, sans-serif;
    font-weight: 700;
    font-size: 6.5px;
    fill: var(--weiss);
  }
</style>
</head>
<body>
<svg class="druckbogen" viewBox="0 0 1200 960" xmlns="http://www.w3.org/2000/svg">
  <!-- Schnittlinien -->
  <line class="schnittlinie" x1="610" y1="57" x2="610" y2="889"/>
  <line class="schnittlinie" x1="40" y1="477" x2="578" y2="477"/>
  <line class="schnittlinie" x1="633" y1="474" x2="1171" y2="474"/>

  <!-- Wimpel 1 -->
  <g class="wimpel">
    <polygon class="wimpel-flaeche" points="57,104 566,243 57,382"/>
    <circle class="stern-feld" cx="158" cy="243" r="80" role="img" aria-label="Sheriffstern mit Band und Stern in der Mitte"/>
    <text class="wimpel-titel" x="244" y="261">POLIZEI</text>
    <text class="wimpel-web" x="84" y="371" transform="rotate(-15.3 84 371)">www.radwimpel-kids.de</text>
  </g>

  <!-- Wimpel 2 -->
  <g class="wimpel">
    <polygon class="wimpel-flaeche" points="654,107 1163,246 654,385"/>
    <circle class="stern-feld" cx="751" cy="246" r="80" role="img" aria-label="Sheriffstern mit Strahlenkranz und Stern in der Mitte"/>
    <text class="wimpel-titel" x="848" y="261">POLIZEI</text>
    <text class="wimpel-web" x="677" y="374" transform="rotate(-15.3 677 374)">www.radwimpel-kids.de</text>
  </g>

  <!-- Wimpel 3 -->
  <g class="wimpel">
    <polygon class="wimpel-flaeche" points="57,560 566,699 57,838"/>
    <circle class="stern-feld" cx="153" cy="697" r="78" role="img" aria-label="Sechszackiger Sheriffstern mit kleinem Stern im Kreis"/>
    <text class="wimpel-titel" x="243" y="716">POLIZEI</text>
    <text class="wimpel-web" x="78" y="827" transform="rotate(-15.3 78 827)">www.radwimpel-kids.de</text>
  </g>

  <!-- Wimpel 4 -->
  <g class="wimpel">
    <polygon class="wimpel-flaeche" points="654,560 1163,699 654,838"/>
    <circle class="stern-feld" cx="750" cy="697" r="78" role="img" aria-label="Sechszackiger Sheriffstern mit großem Stern in der Mitte"/>
    <text class="wimpel-titel" x="836" y="716">POLIZEI</text>
    <text class="wimpel-web" x="675" y="827" transform="rotate(-15.3 675 827)">www.radwimpel-kids.de</text>
  </g>
</svg>
</body>
</html>
```